Brindle Haulage Heavy Goods Transport web design

I have a client who requires a new web site design.
They are Brindle Haulage in the UK.
They have a current site which needs updating with a fresh look and feel using modern design ideas.
Their current site is brindlehaulage.co.uk
I will use your design to build a new CMS site for them using Django.
I only require the layered PSD files, main page design plus a sub page showing navigation changes and layout changes between pages.
The site needs to have the same sections as the current site plus:
1) Proof of delivery downloads system (customer logs in to access their delivery documents).
2) CMS system will allow them to add pages so the menu system needs to be designed such that it can expand.
3) A contact page with a contact form and a Google map will be used.
4) No flash.
5) Slideshow banners (using JQuery will be used).
I like the following type of designs:
www.billoranta.example/pricing.html
www.ledgerpine.example/
vantro.example/features
navkitra.example/
I am looking for a designer to work with me designing other web design projects as well so this project will be used as a test bed for us working together.
The budget for our client designs is between £120 and £200 depending on functionality requirements. This site has a budget of £150.
Please submit your quotes by email to tmarsh@oakvale-studio.example
Target Market(s)
Industrial business customers
Industry/Entity Type
Build
Look and feel

```html
<!DOCTYPE html>
<html lang="en">
<head>
<meta charset="utf-8">
<title>Brindle Haulage – Main</title>
<link rel="stylesheet" href="https://fonts.googleapis.com/css2?family=PT+Sans:ital,wght@0,400;0,700;1,400&family=Questrial&display=swap">
<style>
:root{
  --green-dark:#0f3a0c;
  --green:#1f5a16;
  --green-light:#2f7a22;
  --yellow:#f8c808;
  --yellow-deep:#f2b600;
  --orange:#f59a00;
  --ink:#222;
  --text:#555;
  --page:#f2f2f2;
  --white:#fff;
  --line:#c9c9c9;
}
*{margin:0;padding:0;box-sizing:border-box}
html,body{width:742px;height:1200px;overflow:hidden}
body{position:relative;background:var(--page);font-family:"PT Sans",Arial,sans-serif;color:var(--text)}
.abs{position:absolute}
.header-band{left:0;top:0;width:742px;height:300px;background:radial-gradient(ellipse at 50% 40%,var(--green-light),var(--green) 45%,var(--green-dark) 100%)}
.content-band{left:0;top:545px;width:742px;height:473px;background:var(--white)}
.utility{right:38px;top:4px;font-size:8px;color:#e8f0e6;word-spacing:2px}
.utility span{margin:0 5px;color:#9fb89a}
.brand{left:47px;top:42px;font-family:"Questrial",Arial,sans-serif;font-size:15px;color:var(--white);letter-spacing:.3px}
.search{left:557px;top:52px;width:142px;height:15px;background:var(--white);border:1px solid #ccc;font-size:7px;color:#444;padding:3px 6px}
.search-btn{right:0;top:0;width:18px;height:13px;background:#c4c4c4}
.nav{left:43px;top:81px;width:668px;height:33px;background:linear-gradient(var(--yellow),var(--yellow-deep));display:flex;font-size:10px;color:#3a2c00}
.nav a{display:flex;align-items:center;justify-content:center;border-right:1px solid #d9a300;text-decoration:none;color:inherit}
.nav a.active{background:linear-gradient(#f9b233,var(--orange));color:#2b1a00}
.hero-photo{left:43px;top:114px;width:468px;height:244px;background:linear-gradient(180deg,#c9d4dc 0%,#9fae8f 45%,#223a1e 70%,#6e7064 100%)}
.hero-panel{left:511px;top:114px;width:200px;height:244px;background:linear-gradient(#fbfbfb,#eceeed);border:1px solid #ddd;padding:18px 16px}
.hero-panel h2{font-size:16px;color:#111;font-weight:700;letter-spacing:.5px}
.hero-panel h3{font-size:12px;color:#111;font-weight:400;margin-top:3px;letter-spacing:.3px}
.hero-panel p{font-size:8px;line-height:13px;color:#333;margin-top:6px}
.btn-dark{left:106px;top:203px;width:71px;height:15px;background:var(--green-dark);color:var(--white);font-size:8px;text-align:center;line-height:15px;border-radius:2px}
.dots{left:8px;top:229px;display:flex;gap:2px}
.dots i{width:7px;height:7px;border-radius:50%;background:#111;display:block}
.hero-shadow{left:60px;top:358px;width:640px;height:10px;background:radial-gradient(ellipse at 50% 0,rgba(0,0,0,.25),transparent 70%)}
.feature{top:398px;width:204px;height:122px;background:linear-gradient(var(--yellow),var(--yellow-deep));border:1px solid #e0a800;padding:9px 14px}
.feature h3{font-size:14px;font-weight:400;color:#2a1e00;letter-spacing:.3px}
.feature .rule{height:1px;background:#3a2c00;width:151px;margin:4px 0 7px;position:relative}
.feature .rule:before{content:"";position:absolute;left:0;top:-3px;width:1px;height:7px;background:#3a2c00}
.feature p{font-size:8px;line-height:11.5px;color:#2a1e00;padding-right:16px}
.pill{display:inline-block;margin-top:6px;width:47px;height:10px;background:#111;color:var(--white);font-size:6px;text-align:center;line-height:10px;border-radius:5px}
h2.section{font-size:15px;font-weight:400;color:#222}
.hr{height:1px;background:var(--line)}
.body-copy{font-size:7px;line-height:9px;color:#666}
.body-copy p{margin-bottom:6px}
.body-copy b{color:#333;text-decoration:underline}
.btn-more{width:63px;height:19px;border:1px solid #bbb;border-radius:4px;background:var(--white);font-size:8px;color:#333;line-height:17px;padding-left:7px;box-shadow:0 1px 2px rgba(0,0,0,.15)}
.btn-more span{margin-left:5px}
.service-photo{width:211px;height:77px}
.service-card{width:211px;font-size:7px;line-height:9px;color:#666}
.service-card h4{font-size:7px;color:#2a4a1f;margin-bottom:9px}
.service-card p{margin-bottom:6px}
.list-box{left:514px;top:590px;width:179px;height:230px;background:linear-gradient(#eee,#fafafa);border:1px solid #e2e2e2;padding:10px 10px;font-size:8px;color:#222}
.list-box li{list-style:none;height:13.7px;padding-left:11px;position:relative}
.list-box li:before{content:"";position:absolute;left:2px;top:3px;border-left:3px solid #444;border-top:2px solid transparent;border-bottom:2px solid transparent}
.testimonial{left:515px;top:863px;width:182px;height:117px;background:#ececec;border:1px solid #e0e0e0;padding:9px 12px;font-size:7px;line-height:9px;color:#777;font-style:italic}
.testimonial h4{font-style:normal;color:#333;margin-bottom:5px}
.testimonial p{margin-bottom:5px}
.footer{left:0;top:1018px;width:742px;height:182px;background:radial-gradient(ellipse at 50% 30%,var(--green),var(--green-dark) 80%)}
.footer h3{font-size:12px;font-weight:400;color:var(--white)}
.footer-links{font-size:7.5px;color:#e5efe2}
.footer-links li{list-style:none;height:16.5px;padding-left:7px;position:relative}
.footer-links li:before{content:"";position:absolute;left:0;top:2px;border-left:3px solid #cfe0c9;border-top:2px solid transparent;border-bottom:2px solid transparent}
.social{width:19px;height:19px;border-radius:3px;background:#4a7cb8}
.social-labels{font-size:7.5px;color:#e5efe2;word-spacing:2px}
.contact{font-size:7.5px;line-height:12px;color:#e5efe2}
.contact b{font-size:9px;color:var(--white)}
.footer-line{left:24px;top:147px;width:694px;height:1px;background:rgba(255,255,255,.15)}
.copyright{right:38px;top:160px;font-size:7.5px;color:#e5efe2;word-spacing:2px}
</style>
</head>
<body>
<div class="abs header-band"></div>
<div class="abs content-band"></div>

<div class="abs utility">Member Log In<span>|</span>Register<span>|</span>Sitemap</div>
<div class="abs brand">BRINDLEHAULAGE.CO.UK</div>
<div class="abs search">type your word here<div class="abs search-btn"></div></div>

<nav class="abs nav">
  <a class="active" style="width:57px">Main</a>
  <a style="width:90px">Introduction</a>
  <a style="width:68px">Culture</a>
  <a style="width:80px">The Team</a>
  <a style="width:62px">Depots</a>
  <a style="width:82px">Contact Details</a>
  <a style="width:110px">Notice Board</a>
  <a style="width:119px;border-right:0">Customer Feedback</a>
</nav>

<div class="abs hero-photo" role="img" aria-label="Two green articulated lorries driving along a country road"></div>
<div class="abs hero-panel">
  <h2>OUR COMPANY</h2>
  <h3>SERVICES HERE..</h3>
  <p>Lanterwick Web Studio is a web service company, offering a wide range of services which range from designing and development, that is covering almost all the fields in the best possible way. To be the best we know what and how to present beautifully the working of the client's need and their advantages be highlighted. We act in accordance with the Industry certified processes</p>
  <div class="abs btn-dark">READ MORE</div>
  <div class="abs dots"><i></i><i></i><i></i><i></i></div>
</div>
<div class="abs hero-shadow"></div>

<div class="abs feature" style="left:41px">
  <h3>WHY CHOOSE US ?</h3><div class="rule"></div>
  <p>Lanterwick Web Studio is a web service company, offering a wide range of services which range from designing and development, that is covering almost all the fields in the best possible way.</p>
  <span class="pill">Read more</span>
</div>
<div class="abs feature" style="left:258px">
  <h3>OUR SERVICES</h3><div class="rule"></div>
  <p>Lanterwick Web Studio is a web service company, offering a wide range of services which range from designing and development, that is covering almost all the fields in the best possible way.</p>
  <span class="pill">Read more</span>
</div>
<div class="abs feature" style="left:474px">
  <h3>CUSTOMER FEEDBACK</h3><div class="rule"></div>
  <p>Lanterwick Web Studio is a web service company, offering a wide range of services which range from designing and development, that is covering almost all the fields in the best possible way.</p>
  <span class="pill">Read more</span>
</div>

<h2 class="abs section" style="left:42px;top:566px">Welcome to Brindle Haulage Website Mainpage</h2>
<div class="abs hr" style="left:42px;top:589px;width:433px"></div>
<div class="abs body-copy" style="left:42px;top:600px;width:433px">
  <p><b>Lanterwick Web Studio is a web service company, offering a wide range of services which range from designing and development, that is covering almost all the fields in the best possible way.</b> To be the best we know what and how to present beautifully the working of the client's need and their advantages be highlighted. We act in accordance with the Industry certified processes to deliver the best to our clients all over the world. Over years we have built a strong reputation in providing website design and web development services.</p>
  <p>Thus, Wanna get ahead in the competition with other websites…. Lanterwick Web Studio provide you with an attractive and most convincing website to enhance your marketing goals.</p>
  <p>The only way to success is through the right path and that's what we provide you. None of the other companies has the result we do. So stick to the best that's how you will be the best don't opt for the second best. Our expertise does not limit itself to web development but also it includes Web Hosting, Search Engine Optimization, E-Commerce. We partner hundreds of organization to enhance their business, marketing and profit goals.</p>
</div>
<div class="abs btn-more" style="left:42px;top:716px">READ MORE<span>›</span></div>

<h2 class="abs section" style="left:42px;top:751px;font-size:13px">Our Customer Services</h2>
<div class="abs hr" style="left:42px;top:768px;width:433px"></div>

<div class="abs service-photo" style="left:40px;top:781px;background:linear-gradient(160deg,#e8e2c0,#7c7a6a 45%,#2d2f2c)" role="img" aria-label="Mechanic working beneath a lorry cab in a workshop"></div>
<div class="abs service-photo" style="left:262px;top:781px;background:linear-gradient(150deg,#d9d6cf,#8b7a66 50%,#3b2f26)" role="img" aria-label="Office worker reviewing delivery paperwork at a desk"></div>

<div class="abs service-card" style="left:40px;top:868px">
  <h4>Lanterwick Web Studio is a web service company,</h4>
  <p>offering a wide range of services which range from designing and development, that is covering almost all the fields in the best possible way.</p>
  <p>To be the best we know what and how to present beautifully the working of the client's need and their advantages be highlighted. We act in accordance with the Industry certified processes to deliver the best to our clients all over the world. Over years we have built a strong reputation in providing website design and web development services.</p>
</div>
<div class="abs service-card" style="left:262px;top:868px">
  <h4>Lanterwick Web Studio is a web service company,</h4>
  <p>offering a wide range of services which range from designing and development, that is covering almost all the fields in the best possible way.</p>
  <p>To be the best we know what and how to present beautifully the working of the client's need and their advantages be highlighted. We act in accordance with the Industry certified processes to deliver the best to our clients all over the world. Over years we have built a strong reputation in providing website design and web development services.</p>
</div>
<div class="abs btn-more" style="left:40px;top:978px">READ MORE<span>›</span></div>
<div class="abs btn-more" style="left:261px;top:979px">READ MORE<span>›</span></div>

<h2 class="abs section" style="left:514px;top:567px;font-size:14px">Our Services List</h2>
<ul class="abs list-box">
  <li>Your Company Services goes here..</li>
  <li>CompanyServices goes here..</li>
  <li>Your CompanySecond Services goes here..</li>
  <li>Services Companygoes here..</li>
  <li>Your Company Third Services goes here..</li>
  <li>Company Services goes here..</li>
  <li>Your Company Services goes here..</li>
  <li>Company Services goes here..</li>
  <li>Your Second Services goes here..</li>
  <li>Services goes here..</li>
  <li>Your Thrid Services goes here..</li>
  <li>Company Services goes here..</li>
  <li>Your Second Services goes here..</li>
  <li>Services goes here..</li>
  <li>Your Thrid Services goes here..</li>
</ul>

<h2 class="abs section" style="left:520px;top:837px;font-size:14px">Testimonials</h2>
<div class="abs testimonial">
  <h4>Lanterwick Web Studio service company,</h4>
  <p>Services which range from designing and development, that is covering almost all the fields in the best possible way.</p>
  <p>To be the best we know what and how to present beautifully the working of the client's need and their advantages be highlighted. We act in accordance with the Industry certified processes to deliver the best to our clients all over the world.</p>
</div>

<footer class="abs footer">
  <h3 class="abs" style="left:44px;top:19px">Company Links</h3>
  <ul class="abs footer-links" style="left:44px;top:45px"><li>Main Page</li><li>About Company</li><li>Services</li><li>The Team</li></ul>
  <ul class="abs footer-links" style="left:122px;top:45px"><li>Introduction</li><li>Notice Board</li><li>Customer Feed Back</li></ul>
  <ul class="abs footer-links" style="left:222px;top:45px"><li>Contact Details</li><li>FAQ &amp; Support</li></ul>

  <h3 class="abs" style="left:337px;top:19px">Connect With Us</h3>
  <div class="abs social" style="left:337px;top:48px"></div>
  <div class="abs social" style="left:361px;top:48px"></div>
  <div class="abs social" style="left:386px;top:48px"></div>
  <div class="abs social-labels" style="left:337px;top:76px">Pinefeed &nbsp;| &nbsp;Chirpline &nbsp;| &nbsp;Worknet</div>

  <h3 class="abs" style="left:513px;top:19px">Contact Information</h3>
  <div class="abs contact" style="left:515px;top:44px;width:210px">
    <b>Brindle Haulage Services (Midlands) Limited</b><br>
    Fernhill Yard, Quarry Lane,<br>
    Ashcombe Green, Nr Tilford, Northbridge, NB4 2QJ<br>
    <div style="height:8px"></div>
    Telephone &nbsp;&nbsp;&nbsp;01632 960418<br>
    FAX &nbsp;&nbsp;&nbsp;&nbsp;&nbsp;&nbsp;&nbsp;&nbsp;&nbsp;&nbsp;&nbsp;&nbsp;&nbsp;&nbsp;01632 960427
  </div>

  <div class="abs footer-line"></div>
  <div class="abs copyright">Copyright © 2012 Company Name &nbsp;| &nbsp;All right reserved</div>
</footer>
</body>
</html>
```